Long webpage to explain and sell a complex concept

Accountancy firm wishes to explain Management Accounting to a Small Business audience. We have written the text, assembled a couple of charts and quotes and some concept photos.
There is a lot of text and it is required to explain this type of accounting.
Rather than have a long single block of text which is less likely to be read, we want to break it up with pictures, appropriate white space, diagrams etc. Someone landing on this page will then scroll down reading the text which is designed to keep you reading more.
The page on the website where this will go is https://www.brindlequay.com.au/services/management-accountants-perth/
So the fonts/colours need to fit in. Notice there is a pallet of colours which can be seen here: https://www.brindlequay.com.au/services/

Target Market(s)

Small Business owners in Perth, Western Australia

Number of Pages Required

1 page

Requirements
Must have
• The look and feel needs to match the website indicated in the description above. However we're happy to make the design of this page more interesting than the rest of the site.

```html
<!DOCTYPE html>
<html lang="en">
<head>
<meta charset="utf-8">
<title>Management Accounting for Small Business</title>
<link rel="stylesheet" href="https://fonts.googleapis.com/css2?family=Open+Sans:wght@300&family=Source+Serif+4:wght@300;400&display=swap">
<style>
  :root{
    --ink:#333333;
    --rule:#9a9a9a;
    --brown:#a35a17;
    --plum:#6c1f6e;
    --olive:#6e701d;
    --bg:#ffffff;
  }
  *{margin:0;padding:0;box-sizing:border-box}
  html,body{width:1200px;height:3762px;overflow:hidden;background:var(--bg)}
  body{position:relative;font-family:"Source Serif 4",Georgia,serif;font-weight:300;color:var(--ink);font-size:17.6px;line-height:38.6px;letter-spacing:-0.1px}
  .abs{position:absolute}
  .heading{font-family:"Open Sans",Arial,sans-serif;font-weight:300;font-size:54px;line-height:72px;letter-spacing:0}
  .heading.right{text-align:right}
  .heading.brown{color:var(--brown)}
  .heading.plum{color:var(--plum)}
  .heading.olive{color:var(--olive)}
  .vrule{position:absolute;width:1.5px;background:var(--rule)}
  .copy p{text-align:justify;margin-bottom:15px}
  .copy.wide p{text-align:left}
  .photo{position:absolute}
  ul.reasons{list-style:none}
  ul.reasons li{position:relative;padding-left:42px}
  ul.reasons li::before{content:"";position:absolute;left:14px;top:17px;width:5px;height:5px;border-radius:50%;background:var(--ink)}
</style>
</head>
<body>

<!-- Section: bank account -->
<h2 class="abs heading right brown" style="left:200px;top:78px;width:323px">Watching<br>the bank<br>account?</h2>
<div class="vrule" style="left:580px;top:69px;height:227px"></div>

<div class="abs copy" style="left:194px;top:346px;width:390px">
  <p>Now while the bank account should be watched (not obsessively), too many business owners ONLY monitor their bank account. So what's wrong with this?</p>
  <p>The problem with the money in your bank account is that much of it might not be yours - either now or in the near future. Similarly, much of your money might currently be in other people's bank accounts.</p>
  <p style="margin-top:28px">If you always paid cash for your supplies, and always received cash from your customers, then your bank account might be a better reflection of what is happening right now.</p>
</div>

<svg class="photo" style="left:610px;top:408px" width="551" height="410" role="img" aria-label="Photo of a classical stone bank facade with columns and carved BANK lettering">
  <defs><linearGradient id="stone" x1="0" y1="0" x2="1" y2="1"><stop offset="0" stop-color="#e9e6e2"/><stop offset="0.55" stop-color="#8d7e70"/><stop offset="1" stop-color="#5b4a3e"/></linearGradient></defs>
  <rect width="551" height="410" fill="url(#stone)"/>
</svg>

<div class="abs copy wide" style="left:194px;top:896px;width:880px">
  <p>But, the moment you send or receive an invoice, you're in the debt business. You are lending to, or borrowing money from, the businesses you exchange invoices with. So you need to know how much you owe, and how much you are owed. These debts could be getting out of control and the bank</p>
</div>

<!-- Section: committed expenses -->
<div class="vrule" style="left:606px;top:1073px;height:266px"></div>
<h2 class="abs heading plum" style="left:662px;top:1087px;width:400px">Committed<br>future<br>expenses</h2>

<svg class="photo" style="left:46px;top:1375px" width="535" height="378" role="img" aria-label="Aerial photo of a cruise ship sailing across a deep blue ocean leaving a white wake">
  <defs><linearGradient id="sea" x1="0" y1="0" x2="0" y2="1"><stop offset="0" stop-color="#cfe0ea"/><stop offset="0.12" stop-color="#4f86b8"/><stop offset="1" stop-color="#0d3c86"/></linearGradient></defs>
  <rect width="535" height="378" fill="url(#sea)"/>
</svg>

<div class="abs copy" style="left:607px;top:1380px;width:390px">
  <p>That's not the only problem. When you take on other commitments to fork out cash in future such as employing staff, buying vehicles or plant, or signing a lease, you're committing to that expense (and hoping you'll be able to cover it when the time comes).</p>
  <p>So you see, the bank account is a very late (and inaccurate) indication of what will happen. Businesses are like ships with large turning</p>
</div>

<div class="abs copy wide" style="left:194px;top:1781px;width:880px">
  <p>circles - even a small business can take many months to turn around if things change quickly.<br>You need as much warning as possible of trouble ahead. [insert image of large ship turning]</p>
  <p style="margin-top:38px">This is where the famous "Profit and Loss" (P&amp;L) report might help.</p>
</div>

<!-- Section: P&L problem -->
<h2 class="abs heading right olive" style="left:80px;top:2012px;width:443px">The Problem with<br>the Profit &amp; Loss<br>Report</h2>
<div class="vrule" style="left:580px;top:2006px;height:224px"></div>

<div class="abs copy" style="left:191px;top:2274px;width:390px">
  <p>The P&amp;L shows you what you earned in the month (or the quarter, or year etc). This is why it is a better indication of your profitability than just the bank transactions (but you still need to read your balance sheet and cash summary - but that's another topic).</p>
  <p style="margin-top:38px">So why not just print off the P&amp;L and other reports directly from your accounting system?</p>
  <p style="margin-top:38px">Assuming your bookkeeper has been entering data into you accounting system regularly (and most SMBs are doing this), why don't we just print off a set of reports (P&amp;L, Balance, Cash etc)?</p>
</div>

<svg class="photo" style="left:606px;top:2380px" width="552" height="411" role="img" aria-label="Photo of a printed profit and loss statement with glasses and a pen, overlaid with a large question mark">
  <defs><linearGradient id="paper" x1="0" y1="0" x2="1" y2="1"><stop offset="0" stop-color="#8a6a5c"/><stop offset="0.4" stop-color="#b9b5b1"/><stop offset="1" stop-color="#8f8a86"/></linearGradient></defs>
  <rect width="552" height="411" fill="url(#paper)"/>
</svg>

<svg class="photo" style="left:64px;top:2906px" width="517" height="417" role="img" aria-label="Cartoon illustration of a surprised purple elephant">
  <rect width="517" height="417" fill="#f3f2f7"/>
  <ellipse cx="270" cy="215" rx="190" ry="170" fill="#8f8bc4"/>
</svg>

<div class="abs copy" style="left:607px;top:2939px;width:440px">
  <p style="width:390px">Now you could certainly do this, but you will likely find that it will report a very high profit on the P&amp;L (sounds great, but unfortunately it's a fantasy). Apart from allocation errors, there are lots of causes for overstating profit. The common reasons:</p>
  <ul class="reasons" style="margin-top:-12px">
    <li>Not including interest in the expenses</li>
    <li>Not including depreciation in the expenses</li>
    <li>Paying working Directors via drawings/loans<br>which don't show up in the expenses</li>
  </ul>
</div>

<div class="abs copy wide" style="left:194px;top:3352px;width:880px">
  <p style="margin-bottom:0">Often P&amp;L profit is understated. Reasons for this include:</p>
  <ul class="reasons" style="margin-left:-2px">
    <li>Stock purchases which are expensed immediately rather than put on the balance sheet</li>
    <li>Plant and equipment expensed right away when they should be depreciated</li>
  </ul>
  <p style="margin-top:15px">Then there is just plain mis-coding. Bookkeepers are used to taking short-cuts which are properly<br>cleaned up at end of financial year when the tax returns are done.</p>
  <p style="margin-top:20px">SO it's very rare that we've even seen a P&amp;L done correctly unless they've been properly prepared<br>for management reports.</p>
</div>

</body>
</html>
```